VitaBraid Web Design. Health and Wellness Industry

We are in process of creating next big Cloud based Health Care Management system. We have created 1st draft of Landing Page design. It is missing curb appeal, jazzy feel and engaging modern look.

Need a talented designer to recreate UI/ UX and take it to the next level.
If you are a creative designer, gifted with vision and imagination, I strongly encourage you to participate.

I want the designers to stay focus on the Landing page
Once we select the winner we will provide other subsequent pages
Follow up pages will be similar simple design

Target Market(s)

Individual Users and small business
Age Group 35-75
Individuals involved in "Health and Fitness" activity tracking, managing etc.

Industry/Entity Type

Health And Wellness

Number of Pages Required

5+ page

Colors
f68e4e
34a6d7

Requirements
Must have
• Super Engaging UI/ UX
• Smart and Contemporary look
• Easy to Navigate
• Folder Style menu bar
• Slideshow
• Social Medial Friendly
• Online Shopping
Nice to have
• Start from the enclosed draft Landing Page Idea.
• Feel Free to include additional frame, information section, Icon etc.

```html
<!DOCTYPE html>
<html lang="en">
<head>
<meta charset="utf-8">
<title>VitaBraid – Medical Emergency</title>
<link href="https://fonts.googleapis.com/css2?family=Open+Sans:wght@400;600;700&display=swap" rel="stylesheet">
<style>
  :root {
    --orange: #f68e4e;
    --blue: #34a6d7;
    --red: #e8402f;
    --ink: #4a4a4a;
    --muted: #8a8a8a;
    --line: #dcdcdc;
    --page: #ececec;
    --panel: #f4f4f4;
    --hero-bg: #eef0f2;
    --footer-bg: #e6e4e1;
    --bottom-bg: #5a5a5a;
    --white: #ffffff;
  }
  * { box-sizing: border-box; margin: 0; padding: 0; }
  html, body { width: 716px; height: 1200px; overflow: hidden; }
  body { font-family: 'Open Sans', sans-serif; color: var(--ink); background: var(--page); position: relative; }

  .site-header { height: 70px; background: var(--white); display: flex; align-items: center; justify-content: space-between; padding: 0 36px; position: relative; }
  .brand { display: flex; align-items: center; gap: 8px; font-size: 26px; font-weight: 700; color: var(--orange); }
  .brand-dot { width: 12px; height: 12px; border-radius: 50%; background: var(--orange); }
  .header-tools { display: flex; align-items: center; gap: 8px; margin-top: 10px; }
  .language { position: absolute; top: 8px; right: 36px; font-size: 9px; color: var(--muted); }
  .search { width: 120px; height: 20px; border: 1px solid var(--line); border-radius: 3px; font-size: 9px; color: var(--muted); padding: 3px 8px; }
  .btn-small { height: 20px; padding: 0 12px; border-radius: 3px; font-size: 9px; font-weight: 700; color: var(--white); display: flex; align-items: center; }
  .btn-login { background: var(--orange); }
  .btn-signup { background: var(--blue); }

  .main-nav { height: 26px; background: var(--panel); border-top: 1px solid var(--line); border-bottom: 1px solid var(--line); display: flex; align-items: stretch; padding-left: 36px; font-size: 9px; font-weight: 600; color: var(--muted); }
  .main-nav a { display: flex; align-items: center; gap: 5px; padding: 0 16px; text-decoration: none; color: inherit; }
  .main-nav a.active { color: var(--orange); background: var(--white); }
  .nav-ico { width: 8px; height: 8px; border-radius: 2px; background: currentColor; opacity: .7; }
  .main-nav .emergency-login { margin-left: auto; margin-right: 36px; background: var(--red); color: var(--white); align-self: center; height: 20px; border-radius: 3px; font-weight: 700; }

  .hero { height: 272px; background: var(--hero-bg); position: relative; overflow: hidden; }
  .hero-art { position: absolute; left: 280px; top: 0; width: 436px; height: 272px; background: radial-gradient(circle at 25% 62%, #2f8fc4 0 26%, transparent 27%), radial-gradient(circle at 50% 55%, #5bbbe4 0 24%, transparent 25%), radial-gradient(circle at 72% 65%, #f68e4e 0 22%, transparent 23%), radial-gradient(circle at 92% 70%, #f7b184 0 20%, transparent 21%), linear-gradient(90deg, #dfe6ea, #f0e3d8); }
  .hero-copy { position: absolute; left: 36px; top: 150px; }
  .hero-title { font-size: 24px; font-weight: 600; color: var(--orange); margin-bottom: 12px; }
  .hero-actions { display: flex; gap: 8px; }
  .btn-outline { height: 24px; padding: 0 14px; border: 1.5px solid var(--orange); border-radius: 12px; font-size: 9px; font-weight: 700; color: var(--orange); display: flex; align-items: center; background: var(--white); }

  .tabs { height: 28px; background: var(--white); border-bottom: 1px solid var(--line); display: flex; padding: 0 36px; font-size: 9px; color: var(--muted); }
  .tabs span { flex: 1; display: flex; align-items: center; justify-content: center; border-right: 1px solid var(--line); white-space: nowrap; }
  .tabs span:first-child { border-left: 1px solid var(--line); }
  .tabs span.active { background: var(--orange); color: var(--white); font-weight: 600; }

  .content-card { position: absolute; left: 60px; top: 408px; width: 596px; height: 550px; background: var(--white); border: 1px solid var(--line); display: flex; }
  .side-menu { width: 190px; background: var(--panel); border-right: 1px solid var(--line); }
  .side-menu div { padding: 14px 14px; font-size: 11px; color: var(--ink); border-bottom: 1px solid var(--line); }
  .side-menu div.active { background: var(--white); margin-right: -1px; }
  .feature-list { flex: 1; padding: 18px 20px 0 22px; position: relative; }
  .feature-heading { font-size: 17px; font-weight: 600; color: var(--ink); margin-bottom: 16px; }
  .feature { display: flex; gap: 16px; height: 110px; }
  .feature svg { flex: none; width: 42px; height: 42px; margin-top: 4px; }
  .feature h3 { font-size: 11px; font-weight: 700; color: var(--ink); margin-bottom: 4px; }
  .feature p { font-size: 9px; line-height: 1.45; color: var(--muted); }
  .see-all { position: absolute; left: 22px; bottom: 14px; font-size: 9px; color: var(--muted); display: flex; align-items: center; gap: 5px; }
  .see-all i { width: 10px; height: 10px; border: 1px solid var(--muted); border-radius: 50%; }

  .site-footer { position: absolute; left: 0; top: 975px; width: 716px; height: 185px; background: var(--footer-bg); display: flex; padding: 22px 36px 0; gap: 28px; }
  .footer-col h4 { display: flex; align-items: center; gap: 6px; font-size: 10px; font-weight: 700; color: var(--ink); margin-bottom: 8px; }
  .footer-col h4 i { width: 18px; height: 18px; border-radius: 50%; border: 1.5px solid var(--orange); }
  .footer-col ul { list-style: none; padding-left: 24px; font-size: 8px; line-height: 1.9; color: var(--muted); }
  .store-badges { margin-left: auto; display: flex; flex-direction: column; gap: 8px; padding-top: 6px; }
  .store-badge { width: 110px; height: 34px; border-radius: 5px; background: #3a3a3a; }

  .bottom-bar { position: absolute; left: 0; top: 1160px; width: 716px; height: 40px; background: var(--bottom-bg); display: flex; align-items: center; justify-content: space-between; padding: 0 36px; font-size: 8px; color: #d6d6d6; line-height: 1.5; }
  .social { display: flex; gap: 5px; }
  .social i { width: 14px; height: 14px; border-radius: 50%; }
</style>
</head>
<body>
  <header class="site-header">
    <div class="brand"><span class="brand-dot"></span>VitaBraid</div>
    <span class="language">English ▾</span>
    <div class="header-tools">
      <div class="search">Search here</div>
      <span class="btn-small btn-login">LOGIN</span>
      <span class="btn-small btn-signup">SIGN UP</span>
    </div>
  </header>

  <nav class="main-nav">
    <a class="active" href="#"><i class="nav-ico"></i>HOME</a>
    <a href="#"><i class="nav-ico"></i>CARECHEST</a>
    <a href="#"><i class="nav-ico"></i>PRODUCTS</a>
    <a href="#"><i class="nav-ico"></i>CAREGIVER</a>
    <a href="#"><i class="nav-ico"></i>COMMUNITY</a>
    <a class="emergency-login" href="#">+ EMERGENCY LOGIN</a>
  </nav>

  <section class="hero">
    <div class="hero-art" role="img" aria-label="Overlapping blue and orange head silhouettes with health icons in speech bubbles"></div>
    <div class="hero-copy">
      <h1 class="hero-title">Medical Emergency</h1>
      <div class="hero-actions">
        <span class="btn-outline">LEARN MORE</span>
        <span class="btn-outline">WATCH VIDEO</span>
      </div>
    </div>
  </section>

  <div class="tabs">
    <span>Overview</span>
    <span>How it works</span>
    <span>Data Synchronization</span>
    <span class="active">Medical Emergency</span>
    <span>Stories</span>
    <span>Get Started</span>
  </div>

  <main class="content-card">
    <aside class="side-menu">
      <div class="active">Medical Emergencies</div>
      <div>How It Works</div>
      <div>Create Your Emergency Profile</div>
    </aside>
    <section class="feature-list">
      <h2 class="feature-heading">Be Prepared for Unexpected emergencies</h2>
      <article class="feature">
        <svg viewBox="0 0 42 42" fill="none" stroke="#f68e4e" stroke-width="2"><rect x="3" y="12" width="24" height="18" rx="2"/><path d="M27 18h7l5 6v6H27z"/><circle cx="11" cy="32" r="3"/><circle cx="32" cy="32" r="3"/><path d="M15 16v10M10 21h10"/></svg>
        <div><h3>Be Prepared for an emergency</h3><p>Keep your vital health details in one secure place so responders and family can act fast when every minute matters. Store allergies, medications, conditions and contacts, and update them anytime from any device you own.</p></div>
      </article>
      <article class="feature">
        <svg viewBox="0 0 42 42" fill="none" stroke="#f68e4e" stroke-width="2"><rect x="12" y="4" width="18" height="32" rx="3"/><path d="M18 31h6"/><path d="M6 22l6-4M6 28l6-2"/></svg>
        <div><h3>Mobile device easy access</h3><p>Open your emergency profile from your phone lock screen or tablet in seconds. No passwords to remember in a crisis, yet your data stays encrypted and private, shared only with the people you choose.</p></div>
      </article>
      <article class="feature">
        <svg viewBox="0 0 42 42" fill="none" stroke="#f68e4e" stroke-width="2"><rect x="8" y="7" width="26" height="31" rx="2"/><rect x="15" y="4" width="12" height="6" rx="1"/><path d="M13 18h16M13 24h16M13 30h10"/></svg>
        <div><h3>Simplify doctor's visit</h3><p>Bring a clear summary of readings, symptoms and medicines to every appointment. Your doctor sees trends from your devices at a glance, so visits are shorter, calmer and focused on what really counts.</p></div>
      </article>
      <article class="feature">
        <svg viewBox="0 0 42 42" fill="none" stroke="#f68e4e" stroke-width="2"><rect x="5" y="13" width="32" height="23" rx="2"/><path d="M15 13V8h12v5M5 22h32"/></svg>
        <div><h3>Travel Safe</h3><p>Travel with peace of mind wherever you go. Your profile works across borders and time zones, giving local care teams the facts they need to treat you safely, even when you cannot speak.</p></div>
      </article>
      <div class="see-all"><i></i>See all</div>
    </section>
  </main>

  <footer class="site-footer">
    <div class="footer-col"><h4><i></i>Company</h4><ul><li>About Us</li><li>The Team</li><li>Careers</li><li>Partners</li><li>Payment Options</li></ul></div>
    <div class="footer-col"><h4><i></i>Products</h4><ul><li>Blood Pressure Monitors</li><li>Wireless Scales</li><li>Fitness Devices</li><li>Glucometer</li><li>More</li></ul></div>
    <div class="footer-col"><h4><i></i>Contacts</h4><ul><li>Support</li><li>Shipping/Returns</li><li>Contact Us</li><li>Investors</li><li>Guidelines</li></ul></div>
    <div class="footer-col"><h4><i></i>Downloads</h4><ul><li>Mobile Apps</li><li>Device Driver</li><li>API</li><li>Paper ID</li><li>Advertisement</li></ul></div>
    <div class="store-badges"><div class="store-badge"></div><div class="store-badge"></div></div>
  </footer>

  <div class="bottom-bar">
    <div>Company Information | Privacy Policy | Terms and Conditions<br>Copyright © 2015 VitaBraid. All Rights Reserved</div>
    <div class="social">
      <i style="background:#3b5998"></i><i style="background:#1da1f2"></i><i style="background:#0e76a8"></i><i style="background:#e52d27"></i><i style="background:#dd4b39"></i><i style="background:#cb2027"></i><i style="background:#2ba84a"></i><i style="background:#f68e4e"></i>
    </div>
  </div>
</body>
</html>
```